LANTERN - and the quiet crafts of everyday life

I´m writing a book about CHANGE and the skills leaders needs to embody the transformation from being amanager to become leaders.
The title of the book in Icelandic is the same as the name of the project (which I want to be used on the designes is:) UPPSPRETTA
(with the subtitle:) og hugrekki hversdagsins

Change is not controlled or managed – Leading effective change is an art form which is one of the big reasons for why 70% of changes within companies fail. The main reason however, is that managers are tasked with managing and directing them. The art form of change is to put it in the hands of leaders who possess the emotional intelligence that is needed – all their other advantages intact – to lead change all the way.

The big problem when it comes to change is that there are too many managers and too few leaders within companies – leaders who possess emotional intelligence which is the most important skill a leader embodies to empower change. A leader has what it takes to empower followership.

A manager tends to push and control, make decisions that he presupposes others to implement the way he expects. An emotionally competent leader leads by example and enhances followership on that journey because of the trust and respect he has earned.

In few words: SOFT SKILLS ARE THE NEW HARD SKILLS!

```html
<!DOCTYPE html>
<html lang="is">
<head>
<meta charset="utf-8">
<title>Uppspretta – kápa</title>
<link rel="stylesheet" href="https://fonts.googleapis.com/css2?family=Barlow+Condensed:wght@300;600&family=Tinos&display=swap">
<style>
  :root {
    --ink: #b5581c;
    --paper: #ffffff;
    --backdrop: #1f1f1f;
    --water-light: #d9eef8;
    --water-deep: #5aa9d6;
    --fish: #f2a23a;
  }
  * { margin: 0; padding: 0; box-sizing: border-box; }
  html, body { width: 1200px; height: 1200px; overflow: hidden; background: var(--backdrop); }
  .cover-spread {
    position: absolute; left: 30px; top: 201px;
    width: 1140px; height: 797px;
    background: var(--paper); color: var(--ink);
  }
  .title { font-family: "Barlow Condensed", sans-serif; font-weight: 600; letter-spacing: 0.02em; }
  .subtitle { font-family: "Barlow Condensed", sans-serif; font-weight: 300; }
  .serif { font-family: "Tinos", serif; }

  /* back cover */
  .back { position: absolute; left: 45px; top: 0; width: 442px; }
  .back .title { position: absolute; top: 58px; width: 100%; text-align: center; font-size: 48px; line-height: 1; }
  .back .subtitle { position: absolute; top: 112px; width: 100%; text-align: center; font-size: 29px; line-height: 1; }
  .blurb { position: absolute; top: 152px; width: 100%; }
  .blurb p {
    font-size: 16.4px; line-height: 22.1px;
    text-align: justify; text-align-last: center;
    margin-bottom: 22px;
  }

  /* spine */
  .spine { position: absolute; left: 548px; top: 0; width: 42px; height: 100%; }
  .spine-text {
    position: absolute; left: 0; width: 42px;
    writing-mode: vertical-rl; display: flex; align-items: center; justify-content: flex-start;
  }
  .spine .title { top: 69px; font-size: 52px; line-height: 42px; letter-spacing: 0.01em; }
  .spine .author { top: 490px; font-size: 27px; line-height: 42px; letter-spacing: 0.27em; }

  /* front cover */
  .front { position: absolute; left: 624px; top: 0; width: 500px; height: 100%; text-align: center; }
  .front .title { position: absolute; top: 52px; width: 100%; font-size: 88px; line-height: 1; }
  .front .subtitle { position: absolute; width: 100%; font-size: 41px; line-height: 1; }
  .front .line-1 { top: 160px; }
  .front .line-2 { top: 219px; }
  .front .line-3 { top: 279px; }
  .front-art { position: absolute; left: 65px; top: 371px; width: 361px; height: 302px; }
  .front .author { position: absolute; top: 714px; width: 100%; font-size: 31px; letter-spacing: 0.34em; padding-left: 0.34em; }
</style>
</head>
<body>
<main class="cover-spread">
  <section class="back">
    <h2 class="title">UPPSPRETTA</h2>
    <p class="subtitle">og hugrekki hversdagsins</p>
    <div class="blurb serif">
      <p>Lorem ipsum dolor sit amet, consectetur adipiscing elit, sed do eiusmod tempor incididunt ut labore et dolore magna aliqua. Quis ipsum suspendisse ultrices gravida. Risus commodo viverra maecenas accumsan lacus vel facilisis. Lorem ipsum dolor sit amet, consectetur adipiscing elit, sed do eiusmod tempor incididunt ut labore et dolore magna aliqua. Quis ipsum suspendisse ultrices gravida. Risus commodo viverra maecenas accumsan lacus vel facilisis.</p>
      <p>Lorem ipsum dolor sit amet, consectetur adipiscing elit, sed do eiusmod tempor incididunt ut labore et dolore magna aliqua. Quis ipsum suspendisse ultrices gravida. Risus commodo viverra maecenas accumsan lacus vel facilisis. Lorem ipsum dolor sit amet, consectetur adipiscing elit, sed do eiusmod tempor incididunt ut labore et dolore magna aliqua. Quis ipsum suspendisse ultrices gravida. Risus commodo viverra maecenas accumsan lacus vel facilisis. Lorem ipsum dolor sit amet, consectetur adipiscing elit, sed do eiusmod tempor incididunt ut labore et dolore magna aliqua. Quis ipsum suspendisse ultrices gravida. Risus commodo viverra maecenas accumsan lacus vel facilisis. s gravida. Risus commodo viverra maecenas accumsan lacus vel facilisis. s gravida. Risus commodo viverra maecenas accumsan lacus vel facilisis.</p>
    </div>
  </section>

  <section class="spine">
    <div class="spine-text title">UPPSPRETTA</div>
    <div class="spine-text author serif">AUTHOR NAME</div>
  </section>

  <section class="front">
    <h1 class="title">UPPSPRETTA</h1>
    <p class="subtitle line-1">og</p>
    <p class="subtitle line-2">hugrekki</p>
    <p class="subtitle line-3">hversdagsins</p>
    <svg class="front-art" viewBox="0 0 361 302" role="img" aria-label="Photograph: goldfish leaping in an arc from a small water-filled glass bowl into a large glass fishbowl">
      <defs>
        <radialGradient id="water" cx="0.5" cy="0.55" r="0.6">
          <stop offset="0" stop-color="var(--water-light)"/>
          <stop offset="1" stop-color="var(--water-deep)"/>
        </radialGradient>
        <linearGradient id="arc" x1="0" y1="1" x2="1" y2="0">
          <stop offset="0" stop-color="var(--fish)" stop-opacity="0"/>
          <stop offset="1" stop-color="var(--fish)" stop-opacity="0.45"/>
        </linearGradient>
      </defs>
      <rect width="361" height="302" fill="url(#arc)" opacity="0.35"/>
      <rect x="0" y="60" width="361" height="242" rx="120" fill="url(#water)" opacity="0.75"/>
    </svg>
    <p class="author serif">AUTHOR NAME</p>
  </section>
</main>
</body>
</html>
```